Floor Inspections and Consulting

We provide inspections and consulting services on various floor coverings, e.g. carpet, hardwood, etc. We also do expert witness work for attorneys due to floor covering failures. We current have a logo, just need it incorporated into a new design. I have examples of cards I have found on the internet that capture my attention and make a statement. I have included our original business card, which in my opinion is terrible, but it does have our logo on it.

```html
<!DOCTYPE html>
<html lang="en">
<head>
<meta charset="utf-8">
<title>Keystone Floor Inspections – Business Card</title>
<link rel="stylesheet" href="https://fonts.googleapis.com/css2?family=Archivo+Black&family=Roboto:wght@400;500&display=swap">
<style>
  :root {
    --page: #d9d9d9;
    --card: #151515;
    --orange: #d2400e;
    --white: #ffffff;
    --grey-text: #cfcfcf;
    --shadow: rgba(0,0,0,0.35);
  }
  * { box-sizing: border-box; margin: 0; padding: 0; }
  html, body {
    width: 1200px; height: 1015px; overflow: hidden;
    background: var(--page);
  }
  .canvas {
    width: 1200px; height: 1015px;
    display: flex; flex-direction: column; align-items: center; justify-content: center;
    gap: 46px;
  }
  .card {
    position: relative;
    width: 770px; height: 440px;
    background: var(--card);
    border-bottom: 4px solid var(--orange);
    box-shadow: 0 10px 24px var(--shadow);
    font-family: "Archivo Black", "Arial Black", sans-serif;
    color: var(--white);
  }
  /* Front face */
  .card-front {
    display: flex; flex-direction: column; align-items: center; justify-content: center;
  }
  .brand {
    display: flex; align-items: center; gap: 18px;
  }
  .brand-square {
    width: 30px; height: 30px; background: var(--orange); flex: none;
  }
  .brand-name {
    color: var(--orange);
    font-size: 34px; line-height: 1.05; letter-spacing: 1px; text-transform: uppercase;
  }
  .brand-band {
    margin-top: 16px;
    width: 470px; padding: 7px 0;
    background: var(--orange);
    color: var(--white);
    font-size: 15px; letter-spacing: 2px; text-transform: uppercase; text-align: center;
  }
  .tagline {
    margin-top: 54px;
    font-size: 23px; letter-spacing: 0.3px;
  }
  /* Back face */
  .card-back { padding: 70px 0 0 110px; }
  .card-back .brand-name { font-size: 30px; }
  .contact-name {
    margin: 38px 0 0 160px;
    color: var(--orange);
    font-size: 26px; letter-spacing: 1px; text-transform: uppercase;
  }
  .contact-list {
    list-style: none;
    margin: 22px 0 0 160px;
    font-family: "Roboto", Arial, sans-serif;
    font-size: 21px; color: var(--grey-text);
  }
  .contact-list li {
    display: flex; align-items: center; gap: 12px; margin-bottom: 9px;
  }
  .contact-icon { width: 22px; height: 22px; flex: none; }
</style>
</head>
<body>
<main class="canvas">

  <section class="card card-front" aria-label="Card front">
    <div class="brand">
      <span class="brand-square"></span>
      <span class="brand-name">Keystone Floor<br>Inspections</span>
    </div>
    <div class="brand-band">Analysis &amp; Consulting</div>
    <p class="tagline">Certified Floor Covering Inspection &amp; Consulting</p>
  </section>

  <section class="card card-back" aria-label="Card back">
    <div class="brand">
      <span class="brand-square"></span>
      <span class="brand-name">Keystone Floor<br>Inspections</span>
    </div>
    <p class="contact-name">Dana Whitmore</p>
    <ul class="contact-list">
      <li>
        <svg class="contact-icon" viewBox="0 0 24 24" aria-hidden="true">
          <rect x="2" y="2" width="20" height="20" rx="3" fill="none" stroke="#d2400e" stroke-width="2"/>
          <path d="M8 6c-1 1-1.5 2.5 0 5s3.5 5 6 6c1.5.5 2.5 0 3-1l-2-2-2 1c-1.5-1-2.5-2-3.5-3.5l1-2-2.5-3.5z" fill="#d2400e"/>
        </svg>
        555-201-4470
      </li>
      <li>
        <svg class="contact-icon" viewBox="0 0 24 24" aria-hidden="true">
          <rect x="2" y="5" width="20" height="14" fill="#d2400e"/>
          <path d="M2 5l10 8 10-8" fill="none" stroke="#151515" stroke-width="1.8"/>
        </svg>
        dana@keystonefloor.com
      </li>
      <li>
        <svg class="contact-icon" viewBox="0 0 24 24" aria-hidden="true">
          <circle cx="12" cy="12" r="10" fill="#d2400e"/>
          <g fill="none" stroke="#151515" stroke-width="1.3">
            <ellipse cx="12" cy="12" rx="4.5" ry="10"/>
            <path d="M2 12h20M4 7h16M4 17h16M12 2v20"/>
          </g>
        </svg>
        www.keystonefloor.com
      </li>
    </ul>
  </section>

</main>
</body>
</html>
```